Need Help having my business card stand out

I am the owner of Birchway Canine Training and would like for my business cards to stand out. I have been trying to keep designing them myself but I can't get what I have in my head on the card. I will try my best to post templates that I like for inspirations. I want something unique but elegant. I don't want in to look cartoony or cheesy. It needs to pop in a pet shop but also in a coffee shop or gym.

Target Market(s)

Dog owners, Married ,No young kids Jr High school kids and up (maybe kids on the way) Executives, Stay at home moms/wives, Small business owners

Industry/Entity Type

Dog Training

Contact Information for Business Card

Lowell Spratt, 281-904-3376, info@birchwaycanine.example, www.birchwaycanine.example

Colors

Designer to choose colors to be used in the design.

Requirements
Must have
• my logo
Should not have
• Cursive lettering

```html
<!DOCTYPE html>
<html lang="en">
<head>
<meta charset="utf-8">
<title>Birchway Canine Training — Business Card</title>
<link href="https://fonts.googleapis.com/css2?family=Lato:wght@400;700&display=swap" rel="stylesheet">
<style>
  :root {
    --page-bg: #c4c4c6;
    --card-black: #0d0d0d;
    --card-white: #f4f4f4;
    --arc-grey: #8a8a8a;
    --rule-grey: #6f6f6f;
    --text-light: #ececec;
    --icon-grey: #5a5a5a;
    --photo-top: #c9cdbf;
    --photo-mid: #a8543f;
    --photo-low: #2b3350;
  }
  html, body {
    margin: 0;
    width: 1200px;
    height: 1200px;
    overflow: hidden;
    background: var(--page-bg);
    font-family: "Lato", sans-serif;
  }
  .canvas { position: relative; width: 1200px; height: 1200px; }
  .card {
    position: absolute;
    width: 700px;
    height: 400px;
    overflow: hidden;
    box-shadow: 0 8px 16px rgba(0,0,0,0.25);
  }
  .card-front { left: 250px; top: 150px; background: var(--card-black); }
  .card-back  { left: 250px; top: 630px; background: var(--card-white); }
  .card-art { position: absolute; inset: 0; }

  .brand-front {
    position: absolute;
    left: 40px;
    top: 58px;
    width: 170px;
    text-align: center;
    color: var(--text-light);
    font-weight: 700;
    font-size: 26px;
    line-height: 1.1;
    letter-spacing: 0.5px;
  }
  .brand-mark {
    display: block;
    width: 14px; height: 14px;
    margin: 0 auto 10px;
    border-radius: 50%;
    background: var(--text-light);
  }
  .contact-list {
    position: absolute;
    left: 38px;
    top: 188px;
    margin: 0; padding: 0;
    list-style: none;
    color: var(--text-light);
    font-size: 17px;
  }
  .contact-item { display: flex; align-items: center; height: 26px; }
  .contact-item.phone { margin-bottom: 26px; }
  .contact-icon {
    width: 16px; height: 16px;
    margin-right: 10px;
    background: var(--icon-grey);
    border-radius: 2px;
    display: flex; align-items: center; justify-content: center;
  }
  .contact-icon svg { width: 10px; height: 10px; }
  .owner-name {
    position: absolute;
    left: 0;
    top: 325px;
    width: 400px;
    display: flex;
    align-items: center;
    color: var(--text-light);
    font-weight: 700;
    font-size: 19px;
    letter-spacing: 0.3px;
  }
  .owner-name .rule { height: 1px; background: var(--rule-grey); }
  .owner-name .rule.left { width: 98px; margin-right: 16px; }
  .owner-name .rule.right { flex: 1; margin-left: 16px; }

  .brand-back {
    position: absolute;
    left: 0; right: 0;
    top: 172px;
    text-align: center;
    color: var(--card-black);
    font-weight: 700;
    font-size: 34px;
    letter-spacing: 0.5px;
  }
  .brand-back .brand-mark { display: inline-block; vertical-align: middle; margin: 0 12px 4px 0; background: var(--card-black); }
</style>
</head>
<body>
<div class="canvas">

  <section class="card card-front">
    <svg class="card-art" viewBox="0 0 700 400" width="700" height="400">
      <defs>
        <linearGradient id="photoTone" x1="0" y1="0" x2="0" y2="1">
          <stop offset="0" stop-color="var(--photo-top)"/>
          <stop offset="0.45" stop-color="var(--photo-mid)"/>
          <stop offset="1" stop-color="var(--photo-low)"/>
        </linearGradient>
      </defs>
      <path d="M418 0 L700 0 L700 400 L450 400 Q330 200 418 0 Z" fill="var(--arc-grey)"/>
      <path role="img" aria-label="Photo of the trainer kneeling beside his shepherd dog outdoors"
            d="M432 0 L700 0 L700 400 L464 400 Q346 200 432 0 Z" fill="url(#photoTone)"/>
    </svg>

    <div class="brand-front"><span class="brand-mark"></span>Birchway<br>Canine<br>Training</div>

    <ul class="contact-list">
      <li class="contact-item phone">
        <span class="contact-icon"><svg viewBox="0 0 10 10"><path d="M2 1 L4 1 L4.5 3 L3.5 4 Q4.5 6 6 6.5 L7 5.5 L9 6 L9 8 Q5 9 1 4 Z" fill="#1a1a1a"/></svg></span>
        281-904-3376
      </li>
      <li class="contact-item email">
        <span class="contact-icon"><svg viewBox="0 0 10 10"><rect x="1" y="2.5" width="8" height="5" fill="none" stroke="#1a1a1a"/><path d="M1 2.5 L5 5.5 L9 2.5" fill="none" stroke="#1a1a1a"/></svg></span>
        info@birchwaycanine.example
      </li>
      <li class="contact-item web">
        <span class="contact-icon"><svg viewBox="0 0 10 10"><circle cx="5" cy="5" r="3.6" fill="none" stroke="#1a1a1a"/><path d="M1.4 5 H8.6 M5 1.4 V8.6" stroke="#1a1a1a"/></svg></span>
        www.birchwaycanine.example
      </li>
    </ul>

    <div class="owner-name"><span class="rule left"></span>LOWELL SPRATT<span class="rule right"></span></div>
  </section>

  <section class="card card-back">
    <svg class="card-art" viewBox="0 0 700 400" width="700" height="400">
      <path d="M0 360 L320 360 Q338 360 350 338 Q362 360 380 360 L700 360 L700 400 L0 400 Z" fill="var(--card-black)"/>
    </svg>
    <div class="brand-back"><span class="brand-mark"></span>Birchway Canine Training</div>
  </section>

</div>
</body>
</html>
```